American cannabis tech company business card design

Pavrel.com is seeking a modern, professional, and brand-aligned business card that represents our company and its core values: Mission, Story, Values, and Impact. As an innovative cannabis company, we want a business card that is not only visually appealing but also serves as a representation of who we are and what we stand for.

Project Scope: Design a double-sided business card that integrates our brand identity and core values. Incorporate our key brand elements, ensuring a sleek and contemporary aesthetic. Visually reflect our core values (Mission, Story, Values, Impact) in a way that is engaging yet professional.

Target Market(s)

Vendors, third parties,

Contact Information for Business Card

Contact details (name, title, email, phone, website, etc.)

Font styles to use
Other font styles liked:
• Caslon, Centra

Colors

Designer to choose colors to be used in the design.

Requirements
Must have
• Pavrel.com logo and branding A creative yet clean way to integrate our core values (Mission, Story, Values, Impact) Modern typography and a well-structured layout
Nice to have
• forest green, grey, white, black
Should not have
• references to marijuana, leafs, plants, or related product

```html
<!DOCTYPE html>
<html lang="en">
<head>
<meta charset="utf-8">
<title>Pavrel Business Card</title>
<link href="https://fonts.googleapis.com/css2?family=Poppins:wght@400;600;800;900&display=swap" rel="stylesheet">
<style>
  :root {
    --forest: #15331a;
    --forest-deep: #14311a;
    --paper-a: #dedede;
    --paper-b: #f1f1f1;
    --ink-light: #e9e9e9;
    --backdrop: #262626;
  }
  * { margin: 0; padding: 0; box-sizing: border-box; }
  html, body { width: 1200px; height: 1200px; overflow: hidden; }
  body {
    background: var(--backdrop);
    font-family: "Poppins", sans-serif;
    position: relative;
  }
  .card {
    position: absolute;
    left: 200px;
    width: 798px;
    height: 454px;
    border-radius: 22px;
    overflow: hidden;
    box-shadow: 0 14px 30px rgba(0,0,0,0.45);
  }
  .card--front { top: 96px; background: var(--forest); }
  .card--back { top: 656px; background: var(--forest-deep); color: var(--ink-light); }

  .front__brand {
    position: absolute; left: 0; top: 0;
    width: 392px; height: 100%;
    background: linear-gradient(160deg, var(--paper-a), var(--paper-b));
    display: flex; align-items: center; justify-content: center;
  }
  .brand-name {
    font-weight: 900;
    font-size: 66px;
    letter-spacing: -1px;
    color: var(--forest);
  }
  .front__details {
    position: absolute; left: 457px; top: 128px;
    color: var(--ink-light);
  }
  .person-name { font-weight: 600; font-size: 38px; line-height: 1.1; letter-spacing: 0.5px; }
  .person-title { font-weight: 400; font-size: 22px; letter-spacing: 0.5px; margin-top: 0; }
  .contact-list { list-style: none; margin-top: 14px; }
  .contact-list li {
    display: flex; align-items: center;
    font-size: 20px; letter-spacing: 0.8px;
    height: 32px;
  }
  .contact-list svg { width: 18px; height: 18px; margin-right: 19px; flex: none; }

  .value-block { position: absolute; }
  .value-block h2 {
    display: inline-block;
    font-weight: 800; font-size: 18px;
    letter-spacing: 0.3px;
    border-bottom: 2px solid var(--ink-light);
    padding-bottom: 1px;
    margin-bottom: 8px;
  }
  .value-block p { font-size: 15.2px; line-height: 18.7px; }
  .block--mission { left: 47px; top: 54px; width: 322px; }
  .block--story { left: 47px; top: 200px; width: 322px; }
  .block--values { left: 402px; top: 54px; width: 326px; }
  .block--impact { left: 402px; top: 237px; width: 362px; }
</style>
</head>
<body>
  <section class="card card--front">
    <div class="front__brand">
      <span class="brand-name">PAVREL</span>
    </div>
    <div class="front__details">
      <div class="person-name">EVAN MARLOW</div>
      <div class="person-title">Co-founder &amp; CEO</div>
      <ul class="contact-list">
        <li>
          <svg viewBox="0 0 24 24" fill="none" stroke="#e9e9e9" stroke-width="2"><path d="M5 3h4l2 5-3 2a12 12 0 0 0 6 6l2-3 5 2v4a2 2 0 0 1-2 2A17 17 0 0 1 3 5a2 2 0 0 1 2-2z"/></svg>
          +1 405-555-0148
        </li>
        <li>
          <svg viewBox="0 0 24 24" fill="#e9e9e9"><path d="M2 5h20v14H2z"/><path d="M2 5l10 8 10-8" stroke="#15331a" stroke-width="2" fill="none"/></svg>
          team@pavrel.com
        </li>
        <li>
          <svg viewBox="0 0 24 24" fill="none" stroke="#e9e9e9" stroke-width="2"><circle cx="12" cy="12" r="9"/><path d="M3 12h18M12 3c3 3 3 15 0 18M12 3c-3 3-3 15 0 18"/></svg>
          pavrel.com
        </li>
      </ul>
    </div>
  </section>

  <section class="card card--back">
    <div class="value-block block--mission">
      <h2>MISSION</h2>
      <p>We think cannabis should be accessible, affordable, convenient, and transparent. But most importantly, we believe in supporting the American farmers who make all of this possible.</p>
    </div>
    <div class="value-block block--story">
      <h2>STORY</h2>
      <p>Founded in 2022 by Evan Marlow and Noah Brenner, Pavrel now has a global team of 200+ full-time employees in addition to our robust network of small, U.S. farmers and manufacturing partners. We've built partnerships with over 50 small American farms, bolstering local economies and promoting sustainable farming practices.</p>
    </div>
    <div class="value-block block--values">
      <h2>VALUES</h2>
      <p>At our core is a commitment to product quality and world-class customer experiences. Our company culture fosters open communication &amp; open doors: everybody here has a voice, &amp; we believe that by investing in both our people &amp; our customers, we all will rise.</p>
    </div>
    <div class="value-block block--impact">
      <h2>IMPACT</h2>
      <p>Social impact is a business pillar, not an afterthought. This year, we've donated tens of thousands of dollars to pet humane societies. We've contributed to the campaigns of politicians who advocate for cannabis, contributing to the broader movement toward recognition &amp; acceptance.</p>
    </div>
  </section>
</body>
</html>
```